Business Card Design for Occupational Medicine Start Up Company

We need to design a professional business card. We are a healthcare company providing occupational medicine services to blue collar industries. We are professional, efficient and high quality service providers.

Target Market(s)

Blue Collar Industry: Shipbuilding, Ports, Trucking Companies; The Executives and Safety Officers for these companies

Industry/Entity Type

Healthcare

Contact Information for Business Card

Logo, Name, Title, Email, Phone

Other font styles liked:
• Please match our Brand Guide

Requirements
Must have
• Our Company Colors and Logo

```html
<!DOCTYPE html>
<html lang="en">
<head>
<meta charset="utf-8">
<title>Crewline Health – Business Card</title>
<link href="https://fonts.googleapis.com/css2?family=Montserrat:wght@400;500;700;800&display=swap" rel="stylesheet">
<style>
  :root {
    --navy: #2b2a7e;
    --blue-deep: #2d3f96;
    --blue-mid: #2a7fc6;
    --blue-light: #3aa6e0;
    --sky: #5aaee0;
    --gold: #f2b233;
    --ink: #2b2b3a;
    --paper: #ffffff;
    --backdrop: #d9dbe0;
  }
  * { box-sizing: border-box; margin: 0; padding: 0; }
  html, body {
    width: 1200px; height: 1186px; overflow: hidden;
    background: var(--backdrop);
    font-family: "Montserrat", sans-serif;
  }
  .sheet {
    position: relative; width: 1200px; height: 1186px;
  }
  .card {
    position: absolute; left: 150px; width: 900px; height: 514px;
    border-radius: 28px; overflow: hidden;
    box-shadow: 0 10px 30px rgba(0,0,0,.18);
  }
  /* Back */
  .card--back {
    top: 58px;
    background: linear-gradient(135deg, var(--blue-deep) 0%, var(--blue-mid) 60%, var(--sky) 100%);
  }
  .card--back .brand {
    position: absolute; left: 0; right: 0; top: 0; bottom: 0;
    display: flex; align-items: center; justify-content: center; gap: 26px;
  }
  .brand__dot {
    width: 70px; height: 70px; border-radius: 50%;
    background: var(--paper);
  }
  .card--back .brand__name {
    color: var(--paper); font-weight: 700; font-size: 62px;
    letter-spacing: 1px; text-transform: uppercase;
  }
  /* Front */
  .card--front {
    top: 614px; background: var(--paper);
  }
  .card__shapes { position: absolute; inset: 0; }
  .front-brand {
    position: absolute; right: 90px; top: 90px;
    display: flex; align-items: center; gap: 16px;
  }
  .front-brand .brand__dot { width: 40px; height: 40px; background: var(--navy); }
  .front-brand .brand__name {
    color: var(--navy); font-weight: 700; font-size: 36px;
    text-transform: uppercase; letter-spacing: .5px;
  }
  .person { position: absolute; left: 52px; top: 252px; }
  .person__name { color: var(--navy); font-weight: 800; font-size: 34px; line-height: 1.1; }
  .person__title { color: var(--ink); font-weight: 500; font-size: 19px; margin-top: 4px; }
  .contact { position: absolute; left: 52px; top: 350px; list-style: none; }
  .contact li {
    display: flex; align-items: center; gap: 14px;
    color: var(--ink); font-size: 20px; font-weight: 500; margin-bottom: 12px;
  }
  .contact svg { width: 20px; height: 20px; fill: var(--blue-mid); }
  .address {
    position: absolute; right: 48px; top: 344px; text-align: right;
    color: var(--ink); font-size: 19px; font-weight: 500; line-height: 1.3;
  }
  .web {
    position: absolute; right: 48px; top: 456px;
    color: var(--paper); font-size: 20px; font-weight: 500;
  }
</style>
</head>
<body>
<main class="sheet">

  <section class="card card--back" aria-label="Business card back">
    <div class="brand">
      <span class="brand__dot"></span>
      <span class="brand__name">Crewline Health</span>
    </div>
  </section>

  <section class="card card--front" aria-label="Business card front">
    <svg class="card__shapes" viewBox="0 0 900 514" width="900" height="514" aria-hidden="true">
      <line x1="52" y1="334" x2="340" y2="334" stroke="var(--blue-light)" stroke-width="3"/>
      <line x1="340" y1="334" x2="620" y2="334" stroke="var(--navy)" stroke-width="3"/>
      <line x1="620" y1="334" x2="852" y2="334" stroke="var(--gold)" stroke-width="3"/>
      <path d="M0,470 H470 C505,470 520,432 548,424 L575,420 C545,436 530,490 488,490 H0 Z" fill="var(--blue-light)"/>
      <path d="M0,514 V498 H500 C560,498 565,420 630,420 H900 V514 Z" fill="var(--navy)"/>
    </svg>

    <div class="front-brand">
      <span class="brand__dot"></span>
      <span class="brand__name">Crewline Health</span>
    </div>

    <div class="person">
      <p class="person__name">Daniel Reyes</p>
      <p class="person__title">CEO &amp; Founder</p>
    </div>

    <ul class="contact">
      <li>
        <svg viewBox="0 0 24 24"><path d="M6.6 10.8a15 15 0 0 0 6.6 6.6l2.2-2.2a1 1 0 0 1 1-.25 11.4 11.4 0 0 0 3.6.57 1 1 0 0 1 1 1V20a1 1 0 0 1-1 1A17 17 0 0 1 3 4a1 1 0 0 1 1-1h3.5a1 1 0 0 1 1 1c0 1.25.2 2.45.57 3.57a1 1 0 0 1-.25 1z"/></svg>
        800-555-0142
      </li>
      <li>
        <svg viewBox="0 0 24 24"><path d="M2 5h20v14H2z M2 5l10 8 10-8" fill="var(--blue-mid)" stroke="#fff" stroke-width="1.5"/></svg>
        hello@crewlinehealth.com
      </li>
    </ul>

    <p class="address">410 Harbor View Rd, #12<br>Fairport, OH 44077</p>
    <p class="web">www.crewlinehealth.com</p>
  </section>

</main>
</body>
</html>
```